Logo and label design for our product coffee scrub

We need a logo design and a packaging label design for our new brand called "Benny Velvetrix". Best design wins 500$

It's a cosmetic brand with initial product "coffee scrub", which is a body peeling made of coffee, himalayan salt and additives. Brand will target young to middle aged women, who we will address with a very sexy and slightly provocative appeal (pictures of women wearing nothing but our coffee scrub - sample attached). Purpose of the coffee scrub is to target cellulite, stretch marks, psoriasis, varicose veins, eczema and acne.

Packaging that we will use will be a brown stand up pouch (attached) with a dimensions width 13cm, height 22cm and with a front and back sticker (dimensions width 7cm, height 14cm, round corners) or sticker that overlaps from front to back.

Looking forward on receiving your ideas!

Target Market(s)

Brand will targeting young to middle aged european women, who we will address with a very sexy and slightly provocative appeal (pictures of women wearing nothing but our coffee scrub - sample attached)

Industry/Entity Type

Product

Requirements
Must have
• Just an idea for the logo writing to use a handwriting font "Benny Velvetrix".

For the front side of packaging label you could use a picture of a women's body wearing a coffee scrub. Label should be very sexy but not vulgar.
Nice to have
• The back side of the label should have a cheesy pick up line and declaration text (just a sample):

hi babe! so you wanna get dirty! just show me the way to your bath. but first let me give you a proper introduction of myself. my name is benny and i'm a coffee scrub wearing nothing but 250g of finest arabic coffee and sweet orange flavour & lots of other good stuff.

by the way I will help you with cellulite, stretch marks, psoriasis, varicose veins, eczema and acne. i’ll smooth your lumps and bumps with brown sugar & sea salt, moisturise and tone your skin with cold pressed sweet almond oil, and use vitamins & minerals to work wonders from the outside in. then i’ll make us both smell good with a little orange essence.

ingredients:
Coffea Robusta Seed Powder (Coffee), Prunus Amygdalus Dulcis (Sweet Almond) Oil, Water (Aqua), Sodium Chloride (Salt), Sucrose (Brown Sugar). All ingredients organic.

net weight: 200 g

best before date:

barcode

```html
<!DOCTYPE html>
<html lang="en">
<head>
<meta charset="utf-8">
<title>Benny Velvetrix – Coffee Scrub Label</title>
<link rel="stylesheet" href="https://fonts.googleapis.com/css2?family=Great+Vibes&display=swap">
<style>
  :root {
    --backdrop: #2b2522;
    --label-edge: #3a302b;
    --photo-light: #f4ece6;
    --photo-skin: #e6bfa3;
    --photo-coffee: #5a3b28;
    --leaf-green: #9ec53c;
    --leaf-green-deep: #8ab52f;
    --plum-light: #9a4f9c;
    --plum: #7d3483;
    --plum-deep: #6a2670;
    --ink-white: #ffffff;
  }
  * { margin: 0; padding: 0; box-sizing: border-box; }
  html, body {
    width: 1200px;
    height: 2400px;
    overflow: hidden;
    background: var(--backdrop);
  }
  .label {
    position: absolute;
    left: 64px;
    top: 128px;
    width: 1072px;
    height: 2184px;
    border-radius: 56px;
    overflow: hidden;
    background: var(--plum);
  }
  .label__photo {
    position: absolute;
    left: 0;
    top: 0;
    width: 1072px;
    height: 960px;
    background:
      radial-gradient(ellipse 420px 240px at 300px 170px, rgba(90,59,40,0.55), rgba(90,59,40,0) 70%),
      radial-gradient(ellipse 520px 340px at 560px 360px, var(--photo-skin), rgba(230,191,163,0) 75%),
      radial-gradient(ellipse 260px 160px at 880px 700px, rgba(90,59,40,0.7), rgba(90,59,40,0) 70%),
      linear-gradient(180deg, var(--photo-light) 0%, #eddcd0 55%, #d9b89f 100%);
  }
  .label__waves {
    position: absolute;
    left: 0;
    top: 0;
    width: 1072px;
    height: 2184px;
  }
  .brand-name {
    position: absolute;
    left: 0;
    width: 1072px;
    top: 1480px;
    text-align: center;
    font-family: "Great Vibes", cursive;
    font-size: 150px;
    line-height: 1;
    color: var(--ink-white);
  }
  .product-name {
    position: absolute;
    left: 0;
    width: 1072px;
    top: 1990px;
    text-align: center;
    font-family: "Great Vibes", cursive;
    font-size: 104px;
    line-height: 1;
    color: var(--ink-white);
  }
</style>
</head>
<body>
  <main class="label">
    <div class="label__photo" role="img" aria-label="Photo of a smiling woman lying on a spa table with coffee scrub spread on her back, a bowl of coffee beans beside her"></div>

    <svg class="label__waves" viewBox="0 0 1072 2184" aria-hidden="true">
      <defs>
        <linearGradient id="plum-fill" x1="0" y1="0" x2="0" y2="1">
          <stop offset="0" stop-color="var(--plum-light)"/>
          <stop offset="0.5" stop-color="var(--plum)"/>
          <stop offset="1" stop-color="var(--plum-deep)"/>
        </linearGradient>
        <linearGradient id="green-fill" x1="0" y1="0" x2="1" y2="1">
          <stop offset="0" stop-color="var(--leaf-green)"/>
          <stop offset="1" stop-color="var(--leaf-green-deep)"/>
        </linearGradient>
      </defs>
      <path class="wave-green"
            d="M0 412 C 300 480, 700 560, 1072 800 L 1072 2184 L 0 2184 Z"
            fill="url(#green-fill)"/>
      <path class="wave-plum"
            d="M0 640 C 340 700, 560 980, 760 1300 C 860 1460, 960 1620, 1072 1700 L 1072 2184 L 0 2184 Z"
            fill="url(#plum-fill)"/>
    </svg>

    <h1 class="brand-name">Benny Velvetrix</h1>
    <p class="product-name">coffee scrub</p>
  </main>
</body>
</html>
```